I work in creative/artistic projects across different mediums.
It needs to communicate creativity, style, sexy, uniqueness, individuality and sophistication.
It should not look corporate.
Colours I like are black silver gold deep purple, chocolate, orchid.
It doesn't have to make use of all these colours.
I do not like bright primary colors.
Updates

Project Deadline Extended
Reason: Still in the communication process and to allow the person enough time to finish the design. Though i should know in the next day or two. Thank you.

Target Market(s)

creatives and companies wanting to inject creativity into thier business.

Industry/Entity Type

Work

Contact Information for Business Card

Corwin Haldley
0418592036
corwin@corwinhaldley-example.com

quietgoldenhourstudio.example.au

Requirements
Should not have
• Anything corporate OR OLD FASHIONED

```html
<!DOCTYPE html>
<html lang="en">
<head>
<meta charset="utf-8">
<title>Corwin Haldley — Business Card</title>
<link rel="stylesheet" href="https://fonts.googleapis.com/css2?family=Just+Me+Again+Down+Here&display=swap">
<style>
  :root {
    --slate-blue: #566b92;
    --panel-glow: #4d5e80;
    --panel-edge: #2f3033;
    --charcoal: #2b2a28;
    --ink-white: #ffffff;
    --hand-font: "Just Me Again Down Here", cursive;
  }
  * { margin: 0; padding: 0; box-sizing: border-box; }
  html, body {
    width: 742px;
    height: 1200px;
    overflow: hidden;
    background: var(--charcoal);
  }
  .card {
    position: relative;
    width: 742px;
    height: 1200px;
    font-family: var(--hand-font);
    color: var(--ink-white);
  }
  .card__upper {
    position: absolute;
    left: 0; top: 0;
    width: 742px;
    height: 773px;
    background: var(--slate-blue);
  }
  .card__monogram-panel {
    position: absolute;
    left: 180px; top: 0;
    width: 382px;
    height: 600px;
    background: radial-gradient(ellipse 60% 55% at 50% 45%, var(--panel-glow) 0%, var(--panel-edge) 100%);
    display: flex;
    align-items: center;
    justify-content: center;
  }
  .card__mark-name {
    font-size: 54px;
    line-height: 1;
    text-align: center;
    color: var(--ink-white);
    letter-spacing: 1px;
  }
  .card__name {
    position: absolute;
    left: 0; top: 640px;
    width: 742px;
    text-align: center;
    font-size: 74px;
    line-height: 1;
    letter-spacing: 2px;
  }
  .card__lower {
    position: absolute;
    left: 0; top: 773px;
    width: 742px;
    height: 427px;
    background: var(--charcoal);
  }
  .contact {
    list-style: none;
    position: absolute;
    left: 0; top: 108px;
    width: 742px;
    text-align: center;
  }
  .contact__item {
    font-size: 50px;
    line-height: 68px;
    white-space: nowrap;
    letter-spacing: 1px;
  }
  .contact__item--phone { letter-spacing: 3px; }
</style>
</head>
<body>
  <main class="card">
    <section class="card__upper">
      <div class="card__monogram-panel">
        <span class="card__mark-name">Corwin<br>Haldley</span>
      </div>
      <h1 class="card__name">Corwin Haldley</h1>
    </section>
    <section class="card__lower">
      <ul class="contact">
        <li class="contact__item contact__item--phone">0418592036</li>
        <li class="contact__item contact__item--email">corwin@corwinhaldley-example.com</li>
        <li class="contact__item contact__item--web">quietgoldenhourstudio.example.au</li>
      </ul>
    </section>
  </main>
</body>
</html>
```